Anzeigengestaltung für Fliesenlegermeister
Zielgruppe
Ich bin ein Fliesenlegermeister und möchte mich selbstständig machen, ich saniere Bäder, Böden mit Fliesen, Fliesenspiegel und ich möchte eine Anzeige in den regionalen Zeitungen machen. Ich spreche alle Altersklassen mit Bädern für Sanierungen, Bodenfliesen und Neubauten an. Reparatur und Silikonarbeiten sowie Trockenbauarbeiten am eigenen Heim .
Aufgabenstellung
Ich möchte gern meine Kontaktdaten und die Farben vom Logo wieder finden,
als Beispiel habe ich meine aktuelle Visitenkarte beigefügt Dort finden sich die Kontaktdaten. Meine Arbeiten sind insbesondere :
Fliesenverlegung
Badsanierung
barrierefreie Bäder
Reparaturarbeiten
Silikonarbeiten
Trockenbau
Ob nun genau alle 6 Punkte in der Anzeige angezeigt werden soll bin ich mir nicht sicher oder ob nur 4 Beschreibungen reichen, damit es nicht zu viel wird.

```html
<!DOCTYPE html>
<html lang="de">
<head>
<meta charset="utf-8">
<title>Anzeige Fliesenlegermeister Jonas Brettke</title>
<link href="https://fonts.googleapis.com/css2?family=Montserrat:wght@500;600;700&display=swap" rel="stylesheet">
<style>
  :root {
    --brand-blue: #1f4c9c;
    --ink: #3a3a3a;
    --bullet: #3d3d3d;
    --paper: #ffffff;
    --tile-light: #ececec;
    --tile-mid: #d4d4d4;
  }
  html, body {
    margin: 0;
    padding: 0;
    width: 1200px;
    height: 748px;
    overflow: hidden;
    background: var(--paper);
    font-family: "Montserrat", Arial, sans-serif;
  }
  .ad {
    position: relative;
    width: 1200px;
    height: 748px;
    background: var(--paper);
    overflow: hidden;
  }
  .tile-pattern {
    position: absolute;
    inset: 0;
    background: linear-gradient(135deg, var(--paper) 0%, var(--tile-light) 35%, var(--tile-mid) 100%);
  }
  .brand {
    position: absolute;
    left: 80px;
    top: 60px;
    display: flex;
    align-items: center;
    gap: 22px;
  }
  .brand-square {
    width: 64px;
    height: 64px;
    background: var(--brand-blue);
  }
  .brand-divider {
    width: 3px;
    height: 84px;
    background: var(--ink);
  }
  .brand-name {
    margin: 0;
    font-weight: 700;
    font-size: 58px;
    letter-spacing: 3px;
    line-height: 1;
    color: var(--brand-blue);
    text-transform: uppercase;
  }
  .brand-title {
    margin: 8px 0 0;
    font-weight: 600;
    font-size: 25px;
    letter-spacing: 7px;
    color: var(--ink);
    text-transform: uppercase;
  }
  .services {
    position: absolute;
    left: 110px;
    top: 210px;
    margin: 0;
    padding: 0;
    list-style: none;
  }
  .service {
    display: flex;
    align-items: center;
    gap: 26px;
    height: 54px;
    font-weight: 600;
    font-size: 40px;
    letter-spacing: 1px;
    color: var(--brand-blue);
    text-transform: uppercase;
  }
  .service::before {
    content: "";
    width: 20px;
    height: 20px;
    background: var(--bullet);
    flex: none;
  }
  .service:nth-child(2) { margin-left: 40px; }
  .service:nth-child(3) { margin-left: 80px; }
  .service:nth-child(4) { margin-left: 120px; }
  .service:nth-child(5) { margin-left: 160px; }
  .service:nth-child(6) { margin-left: 200px; }
  .contact {
    position: absolute;
    left: 80px;
    top: 560px;
    margin: 0;
    padding: 0;
    list-style: none;
  }
  .contact-row {
    display: flex;
    align-items: center;
    gap: 24px;
    height: 58px;
    margin-bottom: 6px;
    font-weight: 500;
    font-size: 27px;
    color: var(--ink);
  }
  .contact-row:nth-child(2) { margin-left: 40px; }
  .contact-row:nth-child(3) { margin-left: 80px; }
  .contact-icon {
    width: 200px;
    height: 50px;
    background: var(--brand-blue);
    display: flex;
    align-items: center;
    justify-content: flex-end;
    padding-right: 22px;
    box-sizing: border-box;
    flex: none;
  }
  .contact-icon svg { width: 28px; height: 28px; }
</style>
</head>
<body>
  <main class="ad">
    <div class="tile-pattern" role="img" aria-label="Dekoratives hellgraues Fliesenmuster im Hintergrund"></div>

    <header class="brand">
      <div class="brand-square"></div>
      <div class="brand-divider"></div>
      <div>
        <h1 class="brand-name">Jonas Brettke</h1>
        <p class="brand-title">Fliesenlegermeister</p>
      </div>
    </header>

    <ul class="services">
      <li class="service">Fliesenverlegung</li>
      <li class="service">Badsanierung</li>
      <li class="service">Barrierefreie Bäder</li>
      <li class="service">Reparaturarbeiten</li>
      <li class="service">Silikonarbeiten</li>
      <li class="service">Trockenbau</li>
    </ul>

    <ul class="contact">
      <li class="contact-row">
        <span class="contact-icon">
          <svg viewBox="0 0 24 24" fill="#fff" aria-hidden="true"><path d="M6.6 10.8a15.1 15.1 0 0 0 6.6 6.6l2.2-2.2c.3-.3.7-.4 1-.2 1.1.4 2.3.6 3.6.6.6 0 1 .4 1 1V20c0 .6-.4 1-1 1A17 17 0 0 1 3 4c0-.6.4-1 1-1h3.5c.6 0 1 .4 1 1 0 1.3.2 2.5.6 3.6.1.3 0 .7-.2 1z"/></svg>
        </span>
        <span>05307/4418290 Mobil 0172/5530914</span>
      </li>
      <li class="contact-row">
        <span class="contact-icon">
          <svg viewBox="0 0 24 24" fill="none" stroke="#fff" stroke-width="2" aria-hidden="true"><rect x="3" y="5" width="18" height="14" rx="1"/><path d="M3 6l9 7 9-7"/></svg>
        </span>
        <span>info@fliesenlegermeister-brettke.de</span>
      </li>
      <li class="contact-row">
        <span class="contact-icon">
          <svg viewBox="0 0 24 24" fill="#fff" aria-hidden="true"><path d="M12 2a7 7 0 0 0-7 7c0 5 7 13 7 13s7-8 7-13a7 7 0 0 0-7-7zm0 9.5A2.5 2.5 0 1 1 12 6.5a2.5 2.5 0 0 1 0 5z"/></svg>
        </span>
        <span>Ahornweg 12, 38110 Braunschweig</span>
      </li>
    </ul>
  </main>
</body>
</html>
```